kmvalerohub website

I need a new homepage design for my current website at www.KMValeroHub.com. I want someone to look at my current website and develop a more appealing homepage... right now the colors don't blend very well and it needs a facelift

Reason: This has been extended to September 10th

```html
<!DOCTYPE html>
<html lang="en">
<head>
<meta charset="utf-8">
<title>KM Valero – Home</title>
<link href="https://fonts.googleapis.com/css2?family=Raleway:wght@300;400;500;600&display=swap" rel="stylesheet">
<style>
:root{
  --pink:#d9105a;
  --pink-soft:#ee6a9b;
  --pink-field:#ef4c87;
  --pink-tab:#f3b3cb;
  --white:#ffffff;
  --gray-band:#ebebeb;
  --gray-box:#e4e4e4;
  --text:#6f6f6f;
  --dark:#2b2b2b;
  --black:#1e1e1e;
}
*{box-sizing:border-box;margin:0;padding:0}
html,body{width:1200px;height:2643px;overflow:hidden;background:var(--white);font-family:"Raleway",Arial,sans-serif;color:var(--text)}
.page{position:relative;width:1200px;height:2643px}
.abs{position:absolute}

/* header */
.site-header{left:0;top:0;width:1200px;height:120px;background:var(--pink)}
.brand{left:100px;top:36px;font-size:40px;font-weight:400;color:var(--white)}
.search{left:714px;top:16px;width:276px;height:34px;border-radius:6px;background:var(--pink-soft)}
.search span{position:absolute;left:12px;top:8px;font-size:14px;color:#fde3ec}
.search svg{position:absolute;right:10px;top:8px}
.header-social{left:1063px;top:17px;width:34px;height:34px;border-radius:50%;background:var(--pink-soft)}
.main-nav{right:90px;top:84px;display:flex;gap:20px;font-size:16px;font-weight:500;color:var(--white)}
.main-nav .active{position:relative}
.main-nav .active::after{content:"";position:absolute;left:50%;bottom:-16px;margin-left:-7px;border:7px solid transparent;border-bottom-color:var(--white)}

/* hero */
.hero{left:0;top:120px;width:1200px;height:662px;background:linear-gradient(90deg,#ececec 0%,#f7f7f7 50%,#efefef 100%)}
.hero-photo{left:0;top:0;width:546px;height:662px;background:linear-gradient(160deg,#f2e7df 0%,#e79ab7 45%,#d62a6a 70%,#e9d8d2 100%)}
.hero-kicker{left:552px;top:172px;font-size:38px;font-weight:300;color:#666}
.hero-title{left:550px;top:224px;font-size:51px;line-height:59px;font-weight:300;color:var(--pink)}
.hero-btn{left:553px;top:393px;width:321px;height:70px;background:#6c6c6c;color:var(--white);font-size:26px;font-weight:400;display:flex;align-items:center;justify-content:center;gap:16px}
.hero-book{left:934px;top:365px;width:123px;height:193px;background:linear-gradient(135deg,#f6d6e2,#d9105a 60%,#8a0c3c);box-shadow:4px 6px 10px rgba(0,0,0,.2)}
.slide-arrow{top:255px;width:41px;height:46px;background:#555;display:flex;align-items:center;justify-content:center}
.slide-arrow.prev{left:0}.slide-arrow.next{right:0}

/* products */
.products{left:0;top:782px;width:1200px;height:423px;background:linear-gradient(var(--white) 0 141px,var(--gray-band) 141px)}
.product-card{top:27px;width:340px;height:231px;background:var(--pink)}
.product-card h3{position:absolute;left:20px;right:20px;top:28px;font-size:17px;font-weight:500;color:var(--white);text-align:center;line-height:21px}
.product-tab{position:absolute;top:100px;width:268px;height:204px;left:36px;background:var(--pink-tab);opacity:.6}
.product-frame{position:absolute;top:88px;left:49px;width:250px;height:233px;background:var(--white);border-bottom:2px solid var(--pink)}
.product-cover{position:absolute;left:60px;top:20px;width:130px;height:192px}
.more-btn{position:absolute;left:100px;top:322px;width:134px;height:34px;background:var(--pink);color:var(--white);font-size:16px;display:flex;align-items:center;justify-content:center}

/* about */
.about-photo{left:90px;top:1276px;width:317px;height:255px;background:linear-gradient(135deg,#f1e9e3,#8b5a43 50%,#efe6df)}
.about-title{left:439px;top:1269px;font-size:33px;font-weight:400;color:var(--pink)}
.about-text{left:439px;top:1326px;width:660px;font-size:19.5px;line-height:33px;font-weight:400;color:var(--text)}
.pink-btn{background:var(--pink);color:var(--white);display:flex;align-items:center;justify-content:center;font-weight:500}
.about-btn{left:439px;top:1482px;width:135px;height:51px;font-size:15px}
.divider{left:40px;top:1566px;width:1120px;height:12px;background:radial-gradient(ellipse at top,rgba(0,0,0,.12),transparent 70%)}

/* content columns */
.col-title{top:1635px;width:305px;font-size:38px;font-weight:400;color:var(--pink);border-bottom:2px solid var(--pink);padding-bottom:6px}
.col-box{top:1695px;width:305px;height:233px;background:var(--gray-box)}
.post{position:absolute;left:8px;width:290px;height:80px}
.post-thumb{position:absolute;left:0;top:0;width:68px;height:76px;background:linear-gradient(135deg,#c9c9c9,#666)}
.post h4{position:absolute;left:78px;top:0;font-size:14px;font-weight:500;color:var(--pink)}
.post time{position:absolute;left:78px;top:18px;font-size:12px;color:#888}
.post p{position:absolute;left:78px;top:33px;width:208px;font-size:12.5px;line-height:16px;color:#333}
.media-thumb{position:absolute;left:45px;top:23px;width:213px;height:152px}
.caret{position:absolute;top:84px;font-size:22px;color:#999}
.view-btn{position:absolute;left:81px;top:196px;width:134px;height:49px;font-size:15px}

/* signup */
.signup{left:0;top:1962px;width:1200px;height:398px;background:var(--pink);color:var(--white);text-align:center}
.signup h2{position:absolute;left:0;right:0;top:52px;font-size:26px;font-weight:400}
.signup p{position:absolute;left:0;right:0;top:112px;font-size:20px;line-height:25px;font-weight:400}
.field{position:absolute;left:419px;width:376px;height:48px;background:var(--pink-field);border-radius:3px;text-align:left;padding:13px 20px;font-size:18px;color:#fdd7e5}
.subscribe{position:absolute;left:495px;top:320px;width:233px;height:51px;background:var(--black);color:var(--white);font-size:19px;display:flex;align-items:center;justify-content:center}

/* press */
.press{left:0;top:2360px;width:1200px;height:154px;display:flex;align-items:center;justify-content:center;gap:46px}
.press-mark{height:40px;background:#cfcfcf;border-radius:4px}

/* footer */
.site-footer{left:0;top:2514px;width:1200px;height:129px;background:var(--dark)}
.footer-nav{position:absolute;left:90px;top:29px;display:flex;gap:16px;font-size:13px;color:#bdbdbd}
.footer-legal{position:absolute;left:90px;top:57px;font-size:12px;color:#6d6d6d}
.copyright{position:absolute;left:90px;top:84px;font-size:12px;color:#6d6d6d}
.footer-social{position:absolute;top:40px;width:43px;height:43px;border-radius:50%;background:#555}
</style>
</head>
<body>
<div class="page">

  <header class="site-header abs">
    <div class="brand abs">KM Valero</div>
    <div class="search abs"><span>Search</span>
      <svg width="18" height="18" viewBox="0 0 18 18"><circle cx="7.5" cy="7.5" r="5.5" fill="none" stroke="#fde3ec" stroke-width="2"/><line x1="11.5" y1="11.5" x2="16" y2="16" stroke="#fde3ec" stroke-width="2.5"/></svg>
    </div>
    <div class="header-social abs" role="img" aria-label="Social profile"></div>
    <nav class="main-nav abs">
      <span class="active">HOME</span><span>PRODUCTS</span><span>ABOUT</span><span>BLOG</span><span>FORUM</span><span>MEDIA ROOM</span><span>SUCCESS STORIES</span>
    </nav>
  </header>

  <section class="hero abs">
    <div class="hero-photo abs" role="img" aria-label="Woman in a pink robe seated in a bright bedroom"></div>
    <div class="hero-kicker abs">Discover Secrets to a</div>
    <div class="hero-title abs">Slimmer Sexier &amp;<br>Healthier You !</div>
    <div class="hero-btn abs">View Our Products
      <svg width="34" height="34" viewBox="0 0 34 34"><circle cx="17" cy="17" r="15" fill="none" stroke="#fff" stroke-width="2"/><path d="M9 17h15M18 11l6 6-6 6" fill="none" stroke="#fff" stroke-width="2.5"/></svg>
    </div>
    <div class="hero-book abs" role="img" aria-label="Featured e-book cover"></div>
    <div class="slide-arrow prev abs"><svg width="14" height="24" viewBox="0 0 14 24"><path d="M11 2L3 12l8 10" fill="none" stroke="#fff" stroke-width="2"/></svg></div>
    <div class="slide-arrow next abs"><svg width="14" height="24" viewBox="0 0 14 24"><path d="M3 2l8 10-8 10" fill="none" stroke="#fff" stroke-width="2"/></svg></div>
  </section>

  <section class="products abs">
    <article class="product-card abs" style="left:90px">
      <h3>Lose Weight Without Dieting or Working Out!</h3>
      <div class="product-tab"></div>
      <div class="product-frame"><div class="product-cover" role="img" aria-label="Weight-loss book cover" style="background:linear-gradient(135deg,#f7c1d6,#d9105a 55%,#3a2a2a)"></div></div>
      <div class="more-btn">more</div>
    </article>
    <article class="product-card abs" style="left:430px">
      <h3>Lose Weight Without Dieting or Working Out!</h3>
      <div class="product-tab"></div>
      <div class="product-frame"><div class="product-cover" role="img" aria-label="Fitness guide book cover" style="background:linear-gradient(135deg,#eeeeee,#c9c9c9 50%,#c2273a)"></div></div>
      <div class="more-btn">more</div>
    </article>
    <article class="product-card abs" style="left:770px">
      <h3>Lose Weight Without Dieting or Working Out!</h3>
      <div class="product-tab"></div>
      <div class="product-frame"><div class="product-cover" role="img" aria-label="Healthy recipes book cover" style="background:linear-gradient(160deg,#f2f6ee,#b9d88e 55%,#4d8a36)"></div></div>
      <div class="more-btn">more</div>
    </article>
  </section>

  <div class="about-photo abs" role="img" aria-label="Portrait of KM Valero smiling"></div>
  <h2 class="about-title abs">ABOUT KM VALERO</h2>
  <p class="about-text abs">KM Valero is a nutritionist and certified weight-loss expert, passionate relationship/life coach, and inspirational speaker. She has been featured on The Dawn Hartley Morning Show, The Marcus Vale Show, The Jordan Reese Show, and The Calvin Brooks Show.</p>
  <div class="about-btn pink-btn abs">KNOW MORE</div>
  <div class="divider abs"></div>

  <h2 class="col-title abs" style="left:90px">Latest Blog</h2>
  <div class="col-box abs" style="left:90px">
    <div class="post" style="top:18px"><div class="post-thumb" role="img" aria-label="Blog post thumbnail"></div><h4>I Decided to Live!</h4><time>MAY 27, 2013</time><p>In case you were wondering, where in the world is KM? I wanted.</p></div>
    <div class="post" style="top:117px"><div class="post-thumb" role="img" aria-label="Blog post thumbnail"></div><h4>I Decided to Live!</h4><time>MAY 27, 2013</time><p>In case you were wondering, where in the world is KM? I wanted.</p></div>
  </div>

  <h2 class="col-title abs" style="left:446px">Videos</h2>
  <div class="col-box abs" style="left:446px">
    <span class="caret" style="left:16px">‹</span><span class="caret" style="right:16px">›</span>
    <div class="media-thumb" role="img" aria-label="Television interview video still" style="background:linear-gradient(135deg,#4b3b5a,#8c6b7a 50%,#2a4f8a)"></div>
    <div class="view-btn pink-btn">VIEW ALL</div>
  </div>

  <h2 class="col-title abs" style="left:805px">Photo Gallery</h2>
  <div class="col-box abs" style="left:805px">
    <span class="caret" style="left:16px">‹</span><span class="caret" style="right:16px">›</span>
    <div class="media-thumb" style="left:57px;width:180px;background:linear-gradient(135deg,#b04a3a,#3a2a26 50%,#c9c0b8)" role="img" aria-label="Photo with a talk show host on set"></div>
    <div class="view-btn pink-btn">VIEW ALL</div>
  </div>

  <section class="signup abs">
    <h2>"5 REASONS YOU CAN'T LOSE WEIGHT!"</h2>
    <p>Just enter your name and email below to get instant<br>access to this 30 page report absolutely FREE!</p>
    <div class="field" style="top:185px">Name</div>
    <div class="field" style="top:246px">Email</div>
    <div class="subscribe">SUBSCRIBE</div>
  </section>

  <section class="press abs" aria-label="As featured in">
    <div class="press-mark" style="width:186px"></div>
    <div class="press-mark" style="width:46px"></div>
    <div class="press-mark" style="width:164px"></div>
    <div class="press-mark" style="width:100px"></div>
    <div class="press-mark" style="width:148px"></div>
    <div class="press-mark" style="width:96px"></div>
  </section>

  <footer class="site-footer abs">
    <nav class="footer-nav"><span>HOME</span><span>PRODUCTS</span><span>ABOUT</span><span>BLOG</span><span>FORUM</span><span>MEDIA ROOM</span><span>SUCCESS STORIES</span></nav>
    <div class="footer-legal">Privacy Policy &nbsp;|&nbsp; Terms of Use &nbsp;|&nbsp; Disclaimer</div>
    <div class="copyright">Copyright © 2013 Brightleaf Publishing</div>
    <div class="footer-social" style="left:1011px" role="img" aria-label="Social profile"></div>
    <div class="footer-social" style="left:1060px" role="img" aria-label="Social profile"></div>
  </footer>

</div>
</body>
</html>
```